High Tech Real Estate Startup needs a business card

We are developing an innovative real estate marketing product based around advanced search and virtual reality.

We talk to people, we need business cards.

Target Market(s)

The target market is technology professionals and realtors.

Contact Information for Business Card

The information to be included will include

Name
Title
Phone Number
E-mail Address
www.zelquin.com

It should use simple iconography for each one of those fields.

Font styles to use
Other font styles liked:
• Co, Jubilat, Avenir

Colors

Designer to choose colors to be used in the design.

Requirements
Must have
• Clean aesthetic,
• Good use of negative space.
• It should use our company logo, shown in the attached file. It is able to use the negative of that logo (coloured font and white background) and I have attached other acceptable accent colours in a swatch file.
Should not have
• Should not be too busy
• No extraneous text (slogans, tag lines etc)

```html
<!DOCTYPE html>
<html lang="en">
<head>
<meta charset="UTF-8">
<title>Zelquin Business Card</title>
<link href="https://fonts.googleapis.com/css2?family=Nunito+Sans:wght@400;600&display=swap" rel="stylesheet">
<style>
  :root {
    --canvas-bg: #e4e4e2;
    --card-bg: #ffffff;
    --brand-teal: #13b9c4;
    --ink-slate: #4d6268;
    --card-edge: #d2d2d0;
  }
  * { box-sizing: border-box; margin: 0; padding: 0; }
  html, body {
    width: 1200px;
    height: 1000px;
    overflow: hidden;
    background: var(--canvas-bg);
    font-family: "Nunito Sans", sans-serif;
  }
  .canvas { position: relative; width: 1200px; height: 1000px; }

  .card {
    position: absolute;
    background: var(--card-bg);
    border: 1px solid var(--card-edge);
  }
  .card--front { left: 169px; top: 112px; width: 593px; height: 338px; }
  .card--back  { left: 390px; top: 558px; width: 600px; height: 342px; }

  .brand-name {
    color: var(--brand-teal);
    font-weight: 600;
    letter-spacing: 1px;
    line-height: 1;
    white-space: nowrap;
  }
  .card--front .brand-name {
    position: absolute;
    left: 50%;
    top: 50%;
    transform: translate(-50%, -52%);
    font-size: 64px;
  }
  .card--back .brand-name {
    position: absolute;
    left: 78px;
    top: 171px;
    transform: translate(-50%, -50%) rotate(-90deg);
    font-size: 56px;
  }

  .person {
    position: absolute;
    right: 38px;
    top: 62px;
    text-align: right;
    color: var(--ink-slate);
  }
  .person__name { font-size: 30px; font-weight: 400; line-height: 1.1; }
  .person__title { font-size: 17px; margin-top: 6px; }

  .divider {
    position: absolute;
    left: 137px;
    right: 38px;
    top: 167px;
    height: 2px;
    background: var(--ink-slate);
  }

  .contact-list {
    position: absolute;
    right: 38px;
    top: 209px;
    list-style: none;
    color: var(--ink-slate);
    font-size: 19px;
  }
  .contact-list__item {
    display: flex;
    align-items: center;
    justify-content: flex-end;
    height: 27.5px;
  }
  .contact-list__icon {
    width: 17px;
    height: 17px;
    margin-left: 22px;
    fill: var(--ink-slate);
  }
</style>
</head>
<body>
<div class="canvas">
  <section class="card card--front">
    <div class="brand-name">ZELQUIN</div>
  </section>

  <section class="card card--back">
    <div class="brand-name">ZELQUIN</div>

    <div class="person">
      <div class="person__name">Name of Person</div>
      <div class="person__title">Title of Person</div>
    </div>

    <div class="divider"></div>

    <ul class="contact-list">
      <li class="contact-list__item">
        <span>+123 456 7890</span>
        <svg class="contact-list__icon" viewBox="0 0 24 24" aria-hidden="true">
          <path d="M6.6 10.8c1.4 2.8 3.8 5.1 6.6 6.6l2.2-2.2c.3-.3.7-.4 1-.2 1.1.4 2.3.6 3.6.6.6 0 1 .4 1 1V20c0 .6-.4 1-1 1C10.6 21 3 13.4 3 4c0-.6.4-1 1-1h3.5c.6 0 1 .4 1 1 0 1.3.2 2.5.6 3.6.1.3 0 .7-.2 1l-2.3 2.2z"/>
        </svg>
      </li>
      <li class="contact-list__item">
        <span>www.zelquin.com</span>
        <svg class="contact-list__icon" viewBox="0 0 24 24" aria-hidden="true">
          <path fill="none" stroke="#4d6268" stroke-width="1.8" d="M12 3a9 9 0 1 0 0 18 9 9 0 1 0 0-18zM3 12h18M12 3c2.5 2.5 3.6 5.5 3.6 9s-1.1 6.5-3.6 9c-2.5-2.5-3.6-5.5-3.6-9S9.5 5.5 12 3zM4.5 7.5h15M4.5 16.5h15"/>
        </svg>
      </li>
      <li class="contact-list__item">
        <span>E-mail Address</span>
        <svg class="contact-list__icon" viewBox="0 0 24 24" aria-hidden="true">
          <path d="M2 6h20v12H2z M2.5 6.5 12 13l9.5-6.5" />
          <path d="M2.5 6.8 12 13.2l9.5-6.4" fill="none" stroke="#ffffff" stroke-width="1.4"/>
        </svg>
      </li>
    </ul>
  </section>
</div>
</body>
</html>
```